Business Card Design

We like to use greens as you will see in our logo (but not TOO much green). We are a Dental Clinic in a somewhat eccentric community. We do not like the dated sharp designs which we see many dentists use. We're looking for something bright and fresh while still maintaining the integrity of the profession. Elegance is not necessarily what we are going for... we need for the design to be "mature" but also up-lifting.

See our logo.
Updates

Project Deadline Extended
Reason: We have 5 designs which we like. But we'd like to see a few more before committing to a design.

Project Deadline Extended
Reason: We are awaiting revisions to this project. We are still welcoming designs while we wait to see if designers are able to provide to us the revisions we require in order to proceed with a selection.

Target Market(s)

Younger families - ages late 20's to early 40's

Industry/Entity Type

Business

Contact Information for Business Card

Corwel T. Banfry DDS 2730 W. Halvert Rd. Ste. 7 Royal Oak, MI 48391 (248)555-0174 FX (248)555-0189 info@BrightwellDentalCareMi.com BrigthwellDentalCareMi.com on the back of the card we need an appointment reminder (For____ Date___ Time____) with "If you are unable to keep your appointment, kindly give 48 hours notice" at the bottom. No use of teeth in the design. DOUBLE SIDED DESIGN

Requirements
Should not have
• The use of pictures of teeth

```html
<!DOCTYPE html>
<html lang="en">
<head>
<meta charset="utf-8">
<title>Brightwell Dental Care – Business Card</title>
<link rel="stylesheet" href="https://fonts.googleapis.com/css2?family=Cinzel:wght@400;600&family=Source+Sans+3:ital,wght@0,400;0,600;0,700;1,400;1,600&display=swap">
<style>
  :root {
    --green-dark: #1f6b35;
    --green-mid: #2e8b3e;
    --green-light: #3ea83a;
    --leaf-soft: #8fd06a;
    --ink: #333333;
    --rule: #b9b9b9;
    --card: #ffffff;
    --card-edge: #cfcfcf;
    --backdrop: #ebebe8;
  }
  * { box-sizing: border-box; margin: 0; padding: 0; }
  html, body { width: 1200px; height: 1130px; overflow: hidden; }
  body {
    background: var(--backdrop);
    font-family: "Source Sans 3", "Myriad Pro", Arial, sans-serif;
    color: var(--ink);
    position: relative;
  }
  .card {
    position: absolute;
    width: 878px;
    height: 502px;
    background: var(--card);
    border: 2px solid var(--card-edge);
    border-radius: 30px;
    overflow: hidden;
  }
  .card--front { left: 39px; top: 34px; }
  .card--back { left: 290px; top: 580px; }

  /* Brand name */
  .brand { position: absolute; display: flex; align-items: center; gap: 14px; }
  .brand__dot { width: 30px; height: 30px; border-radius: 50%; background: var(--leaf-soft); flex: none; }
  .brand__name {
    font-family: "Source Sans 3", Arial, sans-serif;
    font-weight: 600;
    color: var(--green-dark);
    line-height: 1.02;
  }
  .card--front .brand { left: 60px; top: 64px; }
  .card--front .brand__name { font-size: 48px; }
  .card--back .brand { right: 50px; top: 38px; gap: 10px; }
  .card--back .brand__name { font-size: 34px; text-align: left; }

  /* Front */
  .holder-name {
    position: absolute; right: 42px; top: 228px;
    font-size: 32px; font-weight: 700; color: var(--green-dark);
  }
  .divider {
    position: absolute; left: 0; right: 0; top: 282px; height: 4px;
    background: linear-gradient(to right, #ffffff 0%, #dcdcdc 35%, var(--rule) 100%);
  }
  .degree { position: absolute; right: 42px; top: 296px; font-size: 24px; }
  .contact-list {
    position: absolute; right: 42px; top: 340px;
    list-style: none; text-align: right; font-size: 21px; line-height: 34px;
  }
  .contact-list li { display: flex; justify-content: flex-end; align-items: center; gap: 6px; }
  .contact-list svg { width: 17px; height: 17px; fill: var(--green-dark); flex: none; }
  .address {
    position: absolute; left: 55px; top: 408px;
    font-size: 21px; line-height: 34px; font-style: normal;
  }

  /* Back */
  .appt-title {
    position: absolute; left: 70px; top: 96px;
    font-family: "Cinzel", "Trajan Pro", serif;
    font-size: 33px; font-weight: 400; color: var(--green-dark); letter-spacing: 0.5px;
  }
  .field { position: absolute; display: flex; align-items: baseline; font-size: 24px; }
  .field__dots { border-bottom: 2px dotted #666; height: 1px; margin: 0 6px; align-self: flex-end; margin-bottom: 7px; }
  .field--name { left: 78px; top: 172px; width: 742px; }
  .field--name .field__dots { flex: 1; margin-left: 14px; }
  .field--date { left: 78px; top: 233px; }
  .dots-date { width: 220px; margin-left: 30px !important; }
  .dots-time { width: 235px; }
  .next-appt { position: absolute; left: 78px; top: 293px; font-size: 24px; }
  .slot {
    position: absolute; top: 293px; height: 36px;
    border: 2px solid #555; border-radius: 5px; background: #fff;
  }
  .slot--1 { left: 318px; width: 158px; }
  .slot--2 { left: 487px; width: 160px; }
  .slot--3 { left: 657px; width: 160px; }
  .weekdays {
    position: absolute; left: 0; right: 0; top: 350px; height: 67px;
    background: linear-gradient(to right, var(--green-dark) 0 669px, var(--green-light) 669px 100%);
  }
  .day {
    position: absolute; top: 0; line-height: 67px;
    color: #fff; font-size: 25px; font-weight: 600;
  }
  .day-box {
    position: absolute; top: 18px; width: 53px; height: 32px;
    background: #fff; border: 2px solid #555; border-radius: 4px;
  }
  .notice {
    position: absolute; left: 0; right: 0; top: 440px; text-align: center;
    font-size: 23px; font-style: italic;
  }
</style>
</head>
<body>

  <section class="card card--front" aria-label="Business card front">
    <div class="brand">
      <span class="brand__dot"></span>
      <span class="brand__name">Brightwell<br>Dental Care</span>
    </div>

    <h1 class="holder-name">Corwel T. Banfry</h1>
    <div class="divider"></div>
    <p class="degree">DDS</p>

    <ul class="contact-list">
      <li><svg viewBox="0 0 24 24" aria-hidden="true"><path d="M6.6 10.8a15.1 15.1 0 0 0 6.6 6.6l2.2-2.2a1 1 0 0 1 1-.25 11.4 11.4 0 0 0 3.6.57 1 1 0 0 1 1 1V20a1 1 0 0 1-1 1A17 17 0 0 1 3 4a1 1 0 0 1 1-1h3.5a1 1 0 0 1 1 1c0 1.25.2 2.45.57 3.6a1 1 0 0 1-.25 1z"/></svg>(248)555-0174</li>
      <li><svg viewBox="0 0 24 24" aria-hidden="true"><path d="M6 3h10v5H6zM3 9h18a1 1 0 0 1 1 1v7a1 1 0 0 1-1 1h-3v3H6v-3H3a1 1 0 0 1-1-1v-7a1 1 0 0 1 1-1zm5 7v3h8v-3z"/></svg>(248)555-0189</li>
      <li><svg viewBox="0 0 24 24" aria-hidden="true"><path d="M2 6h20v12H2zm2 2v.5l8 5 8-5V8l-8 5z"/></svg>info@BrightwellDentalCareMi.com</li>
      <li><svg viewBox="0 0 24 24" aria-hidden="true"><path d="M12 2a10 10 0 1 0 0 20 10 10 0 0 0 0-20zm6.9 9h-3a15 15 0 0 0-1.3-6A8 8 0 0 1 18.9 11zM12 4.1c.9 1.2 1.7 3.7 1.9 6.9h-3.8c.2-3.2 1-5.7 1.9-6.9zM9.4 5a15 15 0 0 0-1.3 6h-3A8 8 0 0 1 9.4 5zm-4.3 8h3a15 15 0 0 0 1.3 6A8 8 0 0 1 5.1 13zm6.9 6.9c-.9-1.2-1.7-3.7-1.9-6.9h3.8c-.2 3.2-1 5.7-1.9 6.9zm2.6-.9a15 15 0 0 0 1.3-6h3a8 8 0 0 1-4.3 6z"/></svg>BrigthwellDentalCareMi.com</li>
    </ul>

    <address class="address">2730 W. Halvert Rd.<br>Ste. 7 Royal Oak, MI 48391</address>
  </section>

  <section class="card card--back" aria-label="Appointment card back">
    <h2 class="appt-title">YOUR APPOINTMENT</h2>
    <div class="brand">
      <span class="brand__dot"></span>
      <span class="brand__name">Brightwell<br>Dental Care</span>
    </div>

    <div class="field field--name">Name :<span class="field__dots"></span></div>
    <div class="field field--date">Date :<span class="field__dots dots-date"></span>Time :<span class="field__dots dots-time"></span>am / pm</div>

    <p class="next-appt">Next Appointment</p>
    <span class="slot slot--1"></span>
    <span class="slot slot--2"></span>
    <span class="slot slot--3"></span>

    <div class="weekdays">
      <span class="day" style="left:78px">MON</span><span class="day-box" style="left:154px"></span>
      <span class="day" style="left:219px">TUE</span><span class="day-box" style="left:279px"></span>
      <span class="day" style="left:346px">WED</span><span class="day-box" style="left:417px"></span>
      <span class="day" style="left:484px">THU</span><span class="day-box" style="left:550px"></span>
      <span class="day" style="left:614px">FRI</span><span class="day-box" style="left:666px"></span>
      <span class="day" style="left:732px">SAT</span><span class="day-box" style="left:790px"></span>
    </div>

    <p class="notice">If you are unable to keep your appointment, kindly give 48 hours notice</p>
  </section>

</body>
</html>
```